Verpackungen für Shampoos
Zielgruppe
Wir sind ein kleines Familienunternehmen mit 2-3 Friseurfilialen und Onlineshop im Naturfriseurbereich, arbeiten mit ökologischen, nachhaltigen und natürlichen Produkten und vertreiben unsere eigene Haarbürste. Wir betreiben mit Sol Verde unsere eigene Marke in diesem Bereich. Erste Produkte, wie eine eigene Haarbürste sind bereits vorhanden und entstanden.
Für unsere erste Shampoo Serie suchen wir ein klares, cleanes und hochwertiges Design. Die 200ml Shampooflasche kommt komplett in weiß und besteh aus recyceltem Material. Es soll klar die ökologisch nachhaltige und etwas höherpreisige Marke kommuniziert werden. Dabei sehen wir vom Stil „weniger ist mehr“ als ganz klare Designvorgabe. Anbei auch ein Beispiel von Pavura, die das ganze sehr schön umgesetzt haben.
Die INCI sind noch nicht final. Es wäre schön, wenn hier ein Platzhalter eingefügt würde. Da eine der Hauptzielgruppen auch Österreicher sind, würden wir uns über ein kleines „Made in Austria“ auf der Vorderseite (evtl. ganz unten auf der Flasche) freuen.
Insgesamt sind es vier verschiedene Shampoos, die aus der gleichen Serie stammen. Es wäre schön, wenn man diese auch direkt unterscheiden könnte. Vielleicht durch ein grafisches Element, oder einfach nur durch die verschiedenen Namenserweiterungen. Hier die Aufstellung mit den Erweiterungen:
Es werden 4 verschiedene Shampoos, die Namen sind:
Change - Strapaziertes Haar
Care - Normales Haar
Sensitiv - Empfindliche Kopfhaut
Balancing - Fettiges Haar
Zielgruppe:
Weiblich, 30-60 Jahre, mittleres bis gehobenes Einkommen, nachhaltig, ökologisch, natürlich, legt Wert auf hochwertige Produkte und Dienstleistungen, achtet auf Konsum.
Aufgabenstellung
Die Landingpage zur Bürste ist hier erreichbar (Beispiel):
Vielleicht hilft das etwas um das Design und die Tonality aufzuschnappen: https://sol-verde.de/gold-birch-wildschweinborstenbuerste/
Es wäre super, wenn das Design der Flasche ähnlich klar und strukturiert ist.
Die Shampoos sind komplett vegan und made in Austria. Die beiden Aspekte sollten in Design auch aufgegriffen werden. Da wir einen 4 farbigen Tamponade/Siebdruck auf der Flasche anwenden, stehen leider nicht so viele Farben zur Verfügung (3-4).
Link zur Flasche:
https://www.brumoxa.com/de/kosmetik/varleno/varleno-tubica/flasche-heavy-200ml-24-410-plastik
Des Weiteren kann sich noch am Sol Verde Haarkonzept und unserem Dienstleistungsflyer orientiert werden.
Benefits:
-       Pflegt das Haar, hält es geschmeidig
- Bio Shampoo Konzentrat
-       Die Grundlage für gesunde Kopfhaut und schönes Haar*
-       Vermindert Spliss*
-       Hält die Haare natürlich geschmeidig
-       Regt die Durchblutung der Kopfhaut an
-       Verteilt Nährstoffe von der Wurzel bis in die Spitzen*
-       Verbessert das Kopfhautklima*
-       Für eine gut durchblutete und gesunde Kopfhaut mit glänzenden und
geschmeidigen Haaren*
-       Entfernt Schuppen und abgestorbene Hautpartikel
-       Verbessert natürlich die allgemeine Haarstruktur
-       Entwirrt langes und gelocktes Haar
-       Reinigt die Kopfhaut ohne Chemie*
-       Mehr Volumen im Haar
-       Mehr Stand im Haar durch Kräftigung der Haarbalkmuskulatur
-       Spart Shampoo und hilft Shampoo seltener und weniger zu nutzen
-       Nährstoffversorgung bis in die Haarspitzen
Inhaltsstoffe:
Care
Aloe Vera Direktsaft*, Decyl Glucoside, Coco Glucoside, Lauryl Glucoside, Hopfenextrakt*, Pentylene Glycol green, Meli..

```html
<!DOCTYPE html>
<html lang="de">
<head>
<meta charset="utf-8">
<title>Sol Verde Sensitiv Shampoo – Etikett</title>
<link rel="stylesheet" href="https://fonts.googleapis.com/css2?family=Questrial&display=swap">
<style>
  :root {
    --backdrop: #e9e9e9;
    --label-white: #fbfbfb;
    --sage: #bcdcb9;
    --sage-deep: #a5c9a2;
    --peach: #f2d5ab;
    --ink: #3a3a3a;
    --brand-blue: #6b77b3;
  }
  * { margin: 0; padding: 0; box-sizing: border-box; }
  html, body {
    width: 1200px; height: 1200px; overflow: hidden;
    background: var(--backdrop);
    font-family: "Questrial", sans-serif;
    color: var(--ink);
  }
  .label {
    position: absolute; left: 300px; top: 40px;
    width: 600px; height: 1120px;
    background: var(--label-white);
  }
  .label__swatch {
    position: absolute; left: 40px; top: 50px;
    width: 260px; height: 150px;
    background: var(--sage);
    transform: rotate(-9deg);
  }
  .brand {
    position: absolute; left: 0; top: 235px; width: 600px;
    text-align: center;
    font-size: 38px; line-height: 1; letter-spacing: 0.5px;
    color: var(--brand-blue);
  }
  .accent-blob { position: absolute; left: 450px; top: 370px; }
  .product__name {
    position: absolute; left: 0; top: 420px; width: 600px;
    text-align: center;
    font-size: 96px; font-weight: 400; letter-spacing: 2px; line-height: 1;
    color: #454545;
  }
  .product__use {
    position: absolute; left: 0; top: 535px; width: 600px;
    text-align: center; font-size: 30px; line-height: 1; letter-spacing: 0.5px;
  }
  .product__type {
    position: absolute; left: 0; top: 585px; width: 600px;
    text-align: center; font-size: 20px; line-height: 1; font-style: italic;
  }
  .artwork {
    position: absolute; left: 40px; top: 665px;
    width: 520px; height: 375px;
    border-radius: 24px;
    background: linear-gradient(120deg, var(--peach) 0%, #f5e6cf 45%, var(--sage) 100%);
  }
  .volume {
    position: absolute; left: 0; top: 1065px; width: 600px;
    text-align: center; font-size: 20px; line-height: 1;
  }
</style>
</head>
<body>
  <main class="label">
    <div class="label__swatch"></div>

    <p class="brand">Sol Verde</p>

    <svg class="accent-blob" width="110" height="120" viewBox="0 0 110 120">
      <path d="M20 20 Q45 0 70 4 Q82 10 80 30 Q100 55 92 90 Q82 110 74 100 Q60 70 40 60 Q5 50 20 20 Z" fill="var(--sage-deep)"/>
    </svg>

    <h1 class="product__name">Sensitiv</h1>
    <p class="product__use">Empfindliche Kopfhaut</p>
    <p class="product__type">Shampoo</p>

    <div class="artwork" role="img" aria-label="Linienillustration einer Frau mit pfirsichfarbenen und grünen Formen und einem Blattzweig"></div>

    <p class="volume">250ml</p>
  </main>
</body>
</html>
```